Need A Standard Musical Download Website

We are looking for a talented designer to create a unique web design for our startup Music website called Vorde Sound.
The website should be responsive and filled with some creative stuffs along with bright colors.

Vorde sound is a website loaded with different types of music and capable of downloading the requested music by its users.
There will be categories of music which would be sorted by the genre. They include RnB, Hip-Hop, Afro pop, Pop, Dancehall and Reggae).

DESIGN STYLE/THEME

Creative, trendy, colorful, unique, and easy to use. You have freedom of selecting which ever color suits you. The design must be energetic and attractive.

NAVIGATION

HOME-MUSIC(RnB, Hip hop, Afro pop, POP, dancehall, Reggae)-ARTISTE-NEWS-LOGIN

PAGES REQUIRED
------------
1)Home Page
2)Music

FONTS
GOOGLE FONTS is strongly recommended.

Designers can get inspiration from https://tunabrook.example

Industry/Entity Type

Startup

```html
<!DOCTYPE html>
<html lang="en">
<head>
<meta charset="utf-8">
<title>Vorde Sound</title>
<link href="https://fonts.googleapis.com/css2?family=Montserrat:wght@300;400;600;700&family=Open+Sans:wght@400;600&display=swap" rel="stylesheet">
<style>
:root{
  --red:#d81f26;
  --red-dark:#b5161c;
  --ink:#222;
  --muted:#777;
  --light:#f1f1f1;
  --tab:#555;
  --night:#1e1f22;
  --white:#fff;
}
*{box-sizing:border-box;margin:0;padding:0}
html,body{width:1200px;height:2592px;overflow:hidden}
body{font-family:"Open Sans",Arial,sans-serif;color:var(--ink);background:var(--white);position:relative}
.abs{position:absolute}

/* hero */
.hero{position:absolute;left:0;top:0;width:1200px;height:700px;overflow:hidden;
  background:radial-gradient(circle at 85% 25%,#4a6fa8 0,transparent 22%),
  radial-gradient(circle at 10% 60%,#5a4a7a 0,transparent 28%),
  radial-gradient(circle at 45% 45%,#8a6a58 0,transparent 30%),
  linear-gradient(180deg,#1a2030,#10131c)}
.nav{position:absolute;left:0;top:0;width:1200px;height:80px;background:rgba(10,12,18,.55)}
.brand{position:absolute;left:100px;top:24px;font-family:"Montserrat",sans-serif;font-weight:600;font-size:24px;color:var(--white)}
.menu{position:absolute;top:32px;display:flex;font-family:"Montserrat",sans-serif;font-size:15px;color:var(--white)}
.menu span{position:absolute;white-space:nowrap}
.hero-title{position:absolute;top:322px;width:100%;text-align:center;font-family:"Montserrat",sans-serif;font-weight:400;font-size:48px;color:var(--white);letter-spacing:1px}
.controls{position:absolute;left:100px;right:100px;top:668px;height:24px}

/* upcoming */
.section-title{font-family:"Montserrat",sans-serif;font-weight:700;color:var(--red);text-align:center}
.upcoming-title{position:absolute;top:762px;width:100%;font-size:38px}
.lede{position:absolute;left:220px;width:760px;top:832px;font-size:13px;line-height:22px;color:var(--muted);text-align:center}
.card{position:absolute;top:948px;width:304px;height:300px}
.date{position:absolute;right:0;top:0;width:84px;height:92px;background:var(--red);color:var(--white);text-align:center;font-family:"Montserrat",sans-serif}
.date b{display:block;font-size:34px;font-weight:600;line-height:50px;margin-top:6px}
.date i{font-style:normal;font-size:20px}

/* genres */
.genres{position:absolute;left:0;top:1320px;width:1200px;height:320px;background:var(--light)}
.tabs{position:absolute;left:520px;top:0;width:680px;height:48px;background:var(--tab);display:flex}
.tabs span{flex:1;text-align:center;line-height:48px;color:#ddd;font-size:15px}
.tabs .active{background:var(--red);color:var(--white)}
.genre-text{position:absolute;left:560px;width:600px;top:80px;font-size:13px;line-height:22px;color:var(--muted)}
.action{position:absolute;top:228px;width:160px;text-align:center;font-size:14px;color:var(--ink);font-weight:600}
.action svg{display:block;margin:0 auto 14px}

/* compose */
.compose-title{position:absolute;left:100px;width:380px;top:1782px;font-family:"Montserrat",sans-serif;font-size:38px;color:var(--red);text-align:center}
.compose-text{position:absolute;left:100px;width:380px;top:1850px;font-size:13px;line-height:22px;color:var(--muted);text-align:center}
.cta{position:absolute;left:132px;top:1966px;width:308px;height:76px;background:var(--red);color:var(--white);text-align:center;font-family:"Montserrat",sans-serif;padding-top:12px}
.cta .one{font-size:19px;color:#ffd2d2;display:block}
.cta .two{font-size:16px;font-weight:700}
.trial{position:absolute;left:552px;top:1950px;width:110px;height:110px;border-radius:50%;background:var(--red);border:4px solid var(--white);color:var(--white);font-family:"Montserrat",sans-serif;font-weight:700;font-size:20px;line-height:24px;text-align:center;padding-top:28px}

/* follow */
.follow{position:absolute;left:0;top:2140px;width:1200px;height:308px;background:var(--night)}
.follow h2{position:absolute;top:62px;width:100%;text-align:center;font-family:"Montserrat",sans-serif;font-weight:300;font-size:38px;letter-spacing:5px;color:var(--white)}
.social{position:absolute;top:178px;width:64px;height:64px;border-radius:50%;background:#3a3b40}

/* footer */
.footer{position:absolute;left:0;top:2448px;width:1200px;height:144px;background:var(--red);color:var(--white);text-align:center;font-size:12px}
.store{position:absolute;top:18px;width:128px;height:40px;border-radius:6px;background:#111}
.links{position:absolute;top:74px;width:100%;line-height:20px}
.copy{position:absolute;top:118px;width:100%;font-size:11px;opacity:.9}
</style>
</head>
<body>

<header class="hero">
  <div class="abs" role="img" aria-label="Young woman in a hat singing into a vintage microphone under blue stage lights" style="left:0;top:0;width:1200px;height:700px;background:radial-gradient(ellipse at 48% 40%,rgba(150,110,90,.55),transparent 45%)"></div>
  <nav class="nav">
    <div class="brand">Vorde Sound</div>
    <div class="menu">
      <span style="left:548px">Home</span>
      <span style="left:660px">Music ▾</span>
      <span style="left:772px">Artiste</span>
      <span style="left:880px">News</span>
      <span style="left:958px">&#9679; Login</span>
      <span style="left:1070px">
        <svg width="16" height="16" viewBox="0 0 16 16"><circle cx="6.5" cy="6.5" r="5" fill="none" stroke="#fff" stroke-width="2"/><line x1="10" y1="10" x2="15" y2="15" stroke="#fff" stroke-width="2"/></svg>
      </span>
    </div>
  </nav>
  <h1 class="hero-title">UNLIMITED PERSONAL CLOUD</h1>
  <svg class="abs" style="left:582px;top:380px" width="36" height="44" viewBox="0 0 36 44"><polygon points="0,0 36,22 0,44" fill="#fff"/></svg>
  <div class="controls">
    <svg width="1000" height="24" viewBox="0 0 1000 24">
      <polygon points="2,5 14,12 2,19" fill="#fff"/>
      <rect x="26" y="6" width="12" height="12" fill="#fff"/>
      <rect x="50" y="10" width="20" height="4" fill="#fff"/>
      <line x1="90" y1="12" x2="960" y2="12" stroke="rgba(255,255,255,.4)" stroke-width="2"/>
      <line x1="90" y1="12" x2="240" y2="12" stroke="#fff" stroke-width="2"/>
      <rect x="978" y="5" width="18" height="14" fill="none" stroke="#fff" stroke-width="2"/>
    </svg>
  </div>
</header>

<section>
  <h2 class="section-title upcoming-title">UPCOMING MUSIC</h2>
  <p class="lede">Since the early days, our editors have gathered the freshest releases from every corner of the scene, so each new week brings tracks worth your time. Browse the upcoming drops below, save the ones you love and get ready to download them the moment they land on Vorde Sound.</p>

  <div class="card" style="left:100px" role="img" aria-label="Concert crowd with raised hands under purple stage lights">
    <div class="abs" style="inset:0;background:radial-gradient(circle at 50% 30%,#e06ad8,#6a1f8a 55%,#2a0d3a)"></div>
    <div class="date"><b>03</b><i>Feb</i></div>
  </div>
  <div class="card" style="left:448px" role="img" aria-label="Vintage microphone with warm golden bokeh">
    <div class="abs" style="inset:0;background:radial-gradient(circle at 50% 45%,#d9a54a,#6b4316 55%,#2a1a0a)"></div>
    <div class="date"><b>13</b><i>Feb</i></div>
  </div>
  <div class="card" style="left:796px" role="img" aria-label="Silhouette of a guitarist against a sunset sky">
    <div class="abs" style="inset:0;background:linear-gradient(180deg,#f6d9a0,#e59a4a 55%,#5a3018)"></div>
    <div class="date"><b>23</b><i>Feb</i></div>
  </div>
</section>

<section class="genres">
  <div class="abs" role="img" aria-label="Street dancers performing in front of a graffiti wall" style="left:0;top:0;width:500px;height:320px;background:linear-gradient(135deg,#8a7a6a,#4a3a30 60%,#2a221c)"></div>
  <div class="tabs">
    <span class="active">Hip Hop</span><span>RnB</span><span>Afro Pop</span><span>POP</span><span>Dancehall</span><span>Reggae</span>
  </div>
  <p class="genre-text">Hip Hop fans will find fresh mixtapes, classic anthems and rising voices here. Stream a preview, build a listen list and keep every favourite track on your device. New beats are added daily by our curators, so check back often for the next big sound.</p>
  <div class="action" style="left:580px">
    <svg width="40" height="36" viewBox="0 0 40 36"><line x1="20" y1="2" x2="20" y2="22" stroke="var(--red)" stroke-width="4"/><polyline points="11,14 20,23 29,14" fill="none" stroke="var(--red)" stroke-width="4"/><polyline points="3,22 3,33 37,33 37,22" fill="none" stroke="var(--red)" stroke-width="4"/></svg>
    Download
  </div>
  <div class="action" style="left:780px">
    <svg width="40" height="36" viewBox="0 0 40 36"><path d="M4 20a16 16 0 0 1 32 0" fill="none" stroke="var(--red)" stroke-width="4"/><rect x="2" y="20" width="8" height="14" fill="var(--red)"/><rect x="30" y="20" width="8" height="14" fill="var(--red)"/></svg>
    Listen List
  </div>
  <div class="action" style="left:980px">
    <svg width="40" height="36" viewBox="0 0 40 36"><rect x="2" y="4" width="36" height="5" fill="var(--red)"/><rect x="2" y="15" width="36" height="5" fill="var(--red)"/><rect x="2" y="26" width="36" height="5" fill="var(--red)"/></svg>
    Add Playlist
  </div>
</section>

<section>
  <h2 class="compose-title">Latest Compose</h2>
  <p class="compose-text">Our in-house writers share their latest compositions every month. Listen to the full session, follow the story behind each song and grab the stems for your own remix.</p>
  <div class="cta"><span class="one">DOWNLOAD UP TO</span><span class="two">25 FREE SONGS* with Trial</span></div>
  <div class="abs" role="img" aria-label="Guitarist playing on a stage lit by bright blue light" style="left:528px;top:1740px;width:560px;height:360px;background:radial-gradient(circle at 75% 20%,#bfe6ff,#2a8ad0 35%,#0d3a6a 75%)"></div>
  <svg class="abs" style="left:772px;top:1888px" width="72" height="50" viewBox="0 0 72 50"><rect width="72" height="50" rx="12" fill="rgba(255,255,255,.85)"/><polygon points="28,14 48,25 28,36" fill="var(--red)"/></svg>
  <div class="trial">FREE<br>TRIAL</div>
</section>

<section class="follow">
  <h2>FOLLOW US</h2>
  <div class="social" style="left:268px"></div>
  <div class="social" style="left:468px"></div>
  <div class="social" style="left:668px"></div>
  <div class="social" style="left:868px"></div>
</section>

<footer class="footer">
  <div class="store" style="left:470px"></div>
  <div class="store" style="left:604px"></div>
  <div class="links">About Vorde Sound &nbsp;|&nbsp; Privacy Policy &nbsp;|&nbsp; Download Manager &nbsp;|&nbsp; Terms of use (updated 10/27/16) &nbsp;|&nbsp; Start Your Trial<br>How it Works &nbsp;|&nbsp; Browse Selection &nbsp;|&nbsp; Why Join? &nbsp;|&nbsp; Affiliate Program &nbsp;|&nbsp; Gift Subscriptions</div>
  <div class="copy">© 2017 Vorde Sound. All Rights Reserved.</div>
</footer>

</body>
</html>
```